LB - WESITE NEEDED PAGE: Clean / Modern / Pro & Dynamic

Lantern-Brokers is a new insurance brokerage firm dealing exclusively with companies (BToB) providing the following property: Liabilities Insurance Insurances Automobile Insurance Insurances Construction% 26amp; Engineering Casualty Workmen 's Compensation Health Insurance Marime% 26amp; Transit Credit Insurance Young, Fast, Proactive and Dynamic we call ourselves Lantern-Brokers because we are a "start-up" willing to make a difference in the market, bringing modernity and speed to our industry, still too bureaucratic / procedural / opaque uninitiated. We need something respecting the colors of our orange logtype; blue; white; black; easy to scroll, with simple information on the company; - who we are - our team (with the pictures) - what we do - what we do - contact us, contact us (google map) Luanda (Angola) Small company, just need something flashy / professional / structured / modern.

Target Market(s)

BtoB; Oil and gas companies; French speaking copying established in Angola, all industrials, factories and importers of goods.

Industry/Entity Type

Insurance Broker

Font styles to use
Sans Serif

Colors

Designer to choose colors to be used in the design.

Requirements
Must have
• We need something respecting the colors of our orange logtype; blue; white; black; easy to scroll, with simple information on the company; - who we are - our team (with the pictures) - what we do - what we do - contact us, contact us (google map) Luanda (Angola) Small company, just need something flashy / professional / structured / modern.
Nice to have
• A page format
Should not have
• WE DO NOT WANT A REFER TO OUR LOGO, but a Home Page for our Website with the basics categories ... >> PLEASE CAREFULLY USE THE RIGHT COLOR OF THE LOGOTYPE which are the ones enclosed Orange / Turquoise / Black as per the business card .

```html
<!DOCTYPE html>
<html lang="en">
<head>
<meta charset="utf-8">
<title>Lantern-Brokers — Insurance Brokerage</title>
<link href="https://fonts.googleapis.com/css2?family=Exo+2:wght@700;800&family=Lato:ital,wght@0,400;0,700;1,400&display=swap" rel="stylesheet">
<style>
:root{
  --orange:#f4532d;
  --orange-light:#ff8a4c;
  --blue:#0a7fd8;
  --blue-dark:#0b63b8;
  --navy:#14223d;
  --ink:#3a3f4a;
  --muted:#6b7180;
  --pale:#f0f3f8;
  --white:#ffffff;
  --grey-icon:#c9ccd2;
  --map-a:#e6e8eb;
  --map-b:#d2d5da;
  --head:"Exo 2",sans-serif;
  --body:"Lato",sans-serif;
}
*{margin:0;padding:0;box-sizing:border-box}
html,body{width:1200px;height:3690px;overflow:hidden}
body{position:relative;background:var(--white);font-family:var(--body);color:var(--ink)}
.abs{position:absolute}
.hero{left:0;top:0;width:1200px;height:793px;background:linear-gradient(160deg,#4a4d55 0%,#2d3038 45%,#5b5e66 100%)}
.brand{left:140px;top:82px;font-weight:700;font-size:18px;color:var(--orange);letter-spacing:.3px;display:flex;align-items:center;gap:8px}
.brand-dot{width:14px;height:14px;border-radius:50%;background:var(--orange)}
.nav{left:0;top:85px;width:1200px;font-weight:700;font-size:12.5px;letter-spacing:.3px}
.nav a{position:absolute;white-space:nowrap;color:var(--white);text-decoration:none}
.nav .active{color:var(--orange)}
.social{display:flex;gap:9px}
.social span{width:31px;height:31px;border-radius:50%;border:2px solid var(--orange);display:block}
.top-social{left:825px;top:21px}
.phone{left:958px;top:20px;display:flex;gap:8px;color:var(--white);font-size:12px;line-height:15px}
.phone b{font-weight:700}
.hero-title{top:363px;left:0;width:1200px;text-align:center;font-family:var(--head);font-weight:800;font-size:38px;color:var(--white);letter-spacing:.5px}
.hero-sub{top:413px;left:0;width:1200px;text-align:center;font-style:italic;font-size:24px;color:var(--white)}
.btn{display:flex;align-items:center;justify-content:center;border-radius:20px;font-weight:700;font-size:12.5px;letter-spacing:.6px;color:var(--white)}
.btn-orange{background:linear-gradient(90deg,var(--orange),var(--orange-light))}
.btn-blue{background:linear-gradient(90deg,var(--blue),var(--blue-dark))}
.section-pale{left:0;top:793px;width:1200px;height:1336px;background:var(--pale)}
.who-photo{left:223px;top:614px;width:378px;height:388px;background:linear-gradient(135deg,#b9c4cc,#7e8c97 55%,#4d5560)}
.who-card{left:601px;top:614px;width:376px;height:388px;background:linear-gradient(160deg,var(--orange-light),var(--orange) 60%,#f23a2a);color:var(--white);padding:64px 34px 0 34px}
.who-card h2{font-family:var(--head);font-weight:800;font-size:30px;margin-bottom:14px}
.who-card .lead{font-weight:700;font-size:13px;line-height:20px;margin-bottom:12px}
.who-card p{font-size:12.5px;line-height:20px;margin-bottom:22px}
.who-card .btn{width:177px;height:36px}
.section-title{left:0;width:1200px;text-align:center;font-family:var(--head);font-weight:800;font-size:34px;color:var(--navy)}
.card{width:282px;height:316px;background:var(--white);box-shadow:0 4px 18px rgba(20,34,61,.08);text-align:center}
.card svg{position:absolute;left:77px;top:35px}
.card h3{position:absolute;top:188px;left:0;width:100%;font-family:var(--head);font-weight:700;font-size:13px;color:var(--navy)}
.card p{position:absolute;top:214px;left:22px;width:238px;font-size:12.5px;line-height:22px;color:var(--muted)}
.member{width:300px;text-align:center}
.member .photo{width:248px;height:248px;border-radius:50%;margin:0 auto;border:4px solid #a4a8b0;background:radial-gradient(circle at 50% 40%,#e6e8eb,#b7bcc4 70%)}
.member.first .photo{border-color:var(--orange)}
.member h4{margin-top:38px;font-family:var(--head);font-weight:800;font-size:18px;color:var(--navy)}
.member p{margin-top:12px;font-size:13px;line-height:20px;color:var(--muted);padding:0 18px}
.member .icons{margin-top:20px;display:flex;justify-content:center;gap:8px}
.member .icons span{width:26px;height:26px;border-radius:50%;background:var(--grey-icon)}
.member.first .icons span{background:var(--blue)}
.map{left:0;top:3238px;width:1200px;height:396px;background:linear-gradient(135deg,var(--map-a),var(--map-b))}
.map-marker{left:566px;top:3428px;width:68px;height:68px;border-radius:8px;background:var(--white);box-shadow:0 4px 14px rgba(20,34,61,.18);display:flex;align-items:center;justify-content:center}
.map-marker span{width:26px;height:26px;border-radius:50%;background:var(--orange)}
.map-pin{left:591px;top:3510px}
.inquiry{left:210px;top:2991px;width:380px;height:389px;background:var(--white);padding:60px 32px 0 34px}
.inquiry h2{font-family:var(--head);font-weight:800;font-size:31px;color:var(--navy);margin-bottom:18px}
.field{height:34px;border:1px solid #e1e4ea;margin-bottom:13px;display:flex;align-items:center;gap:14px;padding-left:12px;font-size:12.5px;color:var(--muted)}
.field i{width:9px;height:9px;background:var(--orange);border-radius:2px;display:block}
.inquiry .btn{width:142px;height:38px;margin-top:8px}
.contact{left:590px;top:2991px;width:375px;height:389px;background:linear-gradient(160deg,var(--orange-light),var(--orange) 60%,#f23a2a);color:var(--white);padding:58px 32px 0 32px}
.contact h2{font-family:var(--head);font-weight:800;font-size:30px;margin-bottom:22px}
.row{display:flex;gap:22px;margin-bottom:28px}
.row svg{flex:none}
.row h5{font-family:var(--head);font-weight:800;font-size:14px;margin:6px 0 6px}
.row div{font-size:12.5px;line-height:18px}
.footer{left:0;top:3634px;width:1200px;height:56px;background:var(--white)}
.copy{left:143px;top:3655px;font-size:11px;color:var(--ink)}
.foot-social{left:946px;top:3648px}
</style>
</head>
<body>

<section class="abs hero" role="img" aria-label="Photo of business people shaking hands over a desk with charts"></section>

<div class="abs brand"><span class="brand-dot"></span>LANTERN-BROKERS</div>

<nav class="abs nav">
  <a class="active" style="left:545px">HOME</a>
  <a style="left:620px">WHO WE ARE</a>
  <a style="left:746px">WHAT WE DO</a>
  <a style="left:871px">OUR TEAM</a>
  <a style="left:978px">CONTACT US</a>
</nav>

<div class="abs social top-social"><span></span><span></span><span></span></div>

<div class="abs phone">
  <svg width="16" height="30" viewBox="0 0 16 30"><rect x="1.5" y="1.5" width="13" height="27" rx="2" fill="none" stroke="#f4532d" stroke-width="2"/><line x1="6" y1="24" x2="10" y2="24" stroke="#f4532d" stroke-width="2"/></svg>
  <div><b>PHONE</b><br>+244 923 000 417</div>
</div>

<h1 class="abs hero-title">YOUNG, FAST, PROACTIVE &amp; DYNAMIC</h1>
<p class="abs hero-sub">We are Insurance brokerage firm dealing exclusively with companies</p>
<a class="abs btn btn-orange" style="left:511px;top:470px;width:176px;height:37px">CONTACT US TODAY</a>

<div class="abs section-pale"></div>

<div class="abs who-photo" role="img" aria-label="Photo of a businessman in an office with analysis charts on screens"></div>
<section class="abs who-card">
  <h2>WHO WE ARE</h2>
  <p class="lead">Lorem ipsum dolor consectetuer adipiscing elit sedda nonummy euismod tincidunt</p>
  <p>Lorem ipsum dolor amet, enim ad minim veniam, quis nostrud exerci tation ullamcorper suscipit lobortis nisl ut aliquip commodo consequat. Duis au tem vel eum iriure dolor in hendrerit vulputate velit esse molestie consequat</p>
  <a class="btn btn-blue">CONTACT US TODAY</a>
</section>

<h2 class="abs section-title" style="top:1126px">WHAT WE DO</h2>

<div class="abs card" style="left:142px;top:1226px">
  <svg width="128" height="128" viewBox="0 0 128 128"><path d="M64 4 A60 60 0 1 0 112 28" fill="none" stroke="#f4532d" stroke-width="5" stroke-linecap="round"/><path d="M118 52 A60 60 0 0 1 100 110" fill="none" stroke="#f4532d" stroke-width="5" stroke-linecap="round"/><circle cx="64" cy="64" r="34" fill="#dbeaf8" role="img" aria-label="Icon of a hand holding an umbrella"/></svg>
  <h3>Liabilities Insurance</h3>
  <p>Lorem ipsum dolor sit amet, enim ad minim veniam, quis nostrud exerci tation ullamcorper suscipit lobortis.</p>
</div>
<div class="abs card" style="left:458px;top:1226px">
  <svg width="128" height="128" viewBox="0 0 128 128"><path d="M64 4 A60 60 0 1 0 112 28" fill="none" stroke="#f4532d" stroke-width="5" stroke-linecap="round"/><path d="M118 52 A60 60 0 0 1 100 110" fill="none" stroke="#f4532d" stroke-width="5" stroke-linecap="round"/><circle cx="64" cy="64" r="34" fill="#dbeaf8" role="img" aria-label="Icon of a car with a shield"/></svg>
  <h3>Automobile Insurance</h3>
  <p>Lorem ipsum dolor sit amet, enim ad minim veniam, quis nostrud exerci tation ullamcorper suscipit lobortis.</p>
</div>
<div class="abs card" style="left:776px;top:1226px">
  <svg width="128" height="128" viewBox="0 0 128 128"><path d="M64 4 A60 60 0 1 0 112 28" fill="none" stroke="#f4532d" stroke-width="5" stroke-linecap="round"/><path d="M118 52 A60 60 0 0 1 100 110" fill="none" stroke="#f4532d" stroke-width="5" stroke-linecap="round"/><circle cx="64" cy="64" r="34" fill="#dbeaf8" role="img" aria-label="Icon of a construction worker and buildings"/></svg>
  <h3>Construction &amp; Engineering Insurance</h3>
  <p>Lorem ipsum dolor sit amet, enim ad minim veniam, quis nostrud exerci tation ullamcorper suscipit lobortis.</p>
</div>
<div class="abs card" style="left:142px;top:1608px">
  <svg width="128" height="128" viewBox="0 0 128 128"><path d="M64 4 A60 60 0 1 0 112 28" fill="none" stroke="#f4532d" stroke-width="5" stroke-linecap="round"/><path d="M118 52 A60 60 0 0 1 100 110" fill="none" stroke="#f4532d" stroke-width="5" stroke-linecap="round"/><circle cx="64" cy="64" r="34" fill="#dbeaf8" role="img" aria-label="Icon of a worker injury with a shield"/></svg>
  <h3>Casualty Workmen 's Compensation</h3>
  <p>Lorem ipsum dolor sit amet, enim ad minim veniam, quis nostrud exerci tation ullamcorper suscipit lobortis.</p>
</div>
<div class="abs card" style="left:458px;top:1608px">
  <svg width="128" height="128" viewBox="0 0 128 128"><path d="M64 4 A60 60 0 1 0 112 28" fill="none" stroke="#f4532d" stroke-width="5" stroke-linecap="round"/><path d="M118 52 A60 60 0 0 1 100 110" fill="none" stroke="#f4532d" stroke-width="5" stroke-linecap="round"/><circle cx="64" cy="64" r="34" fill="#dbeaf8" role="img" aria-label="Icon of a hand holding a medical kit"/></svg>
  <h3>Health Insurance</h3>
  <p>Lorem ipsum dolor sit amet, enim ad minim veniam, quis nostrud exerci tation ullamcorper suscipit lobortis.</p>
</div>
<div class="abs card" style="left:776px;top:1608px">
  <svg width="128" height="128" viewBox="0 0 128 128"><path d="M64 4 A60 60 0 1 0 112 28" fill="none" stroke="#f4532d" stroke-width="5" stroke-linecap="round"/><path d="M118 52 A60 60 0 0 1 100 110" fill="none" stroke="#f4532d" stroke-width="5" stroke-linecap="round"/><circle cx="64" cy="64" r="34" fill="#dbeaf8" role="img" aria-label="Icon of a hand holding a cargo ship"/></svg>
  <h3>Marime &amp; Transit Credit Insurance</h3>
  <p>Lorem ipsum dolor sit amet, enim ad minim veniam, quis nostrud exerci tation ullamcorper suscipit lobortis.</p>
</div>

<a class="abs btn btn-blue" style="left:513px;top:1986px;width:189px;height:37px">CONTACT US TODAY</a>

<h2 class="abs section-title" style="top:2224px">OUR TEAM</h2>

<div class="abs member first" style="left:168px;top:2368px">
  <div class="photo" role="img" aria-label="Portrait photo of a senior team member in a suit"></div>
  <h4>DR. MARCUS DELAINE</h4>
  <p>Advanced Medical and Surgical Glaucoma Managment, Minimally Invasive Glaucoma Surgery</p>
  <div class="icons"><span></span><span></span><span></span></div>
</div>
<div class="abs member" style="left:450px;top:2368px">
  <div class="photo" role="img" aria-label="Portrait photo of a team member with glasses in a suit"></div>
  <h4>DR. TOMAS FERREIRA</h4>
  <p>Advanced Medical and Surgical Glaucoma Management, Minimally Invasive Glaucoma Surgery,...</p>
  <div class="icons"><span></span><span></span><span></span></div>
</div>
<div class="abs member" style="left:731px;top:2368px">
  <div class="photo" role="img" aria-label="Portrait photo of a smiling team member in a suit"></div>
  <h4>DR. ELIAS MONTEIRO</h4>
  <p>All-Laser Cataract Surgery, Refractive Surgery, Comprehensive Ophthalmology</p>
  <div class="icons"><span></span><span></span><span></span></div>
</div>

<a class="abs btn btn-blue" style="left:505px;top:2848px;width:190px;height:37px">CONTACT US TODAY</a>

<div class="abs map" role="img" aria-label="Street map of central Luanda showing the office location"></div>
<div class="abs map-marker"><span></span></div>
<svg class="abs map-pin" width="18" height="24" viewBox="0 0 18 24"><path d="M9 23 C4 15 1 12 1 8 A8 8 0 0 1 17 8 C17 12 14 15 9 23Z" fill="#f23a2a"/><circle cx="9" cy="8" r="3" fill="#fff"/></svg>

<section class="abs inquiry">
  <h2>QUICK INQUIRY</h2>
  <div class="field"><i></i>Name</div>
  <div class="field"><i></i>Phone</div>
  <div class="field"><i></i>Email</div>
  <div class="field"><i></i>Message</div>
  <a class="btn btn-blue">SUBMIT</a>
</section>

<section class="abs contact">
  <h2>CONTACT US</h2>
  <div class="row">
    <svg width="36" height="44" viewBox="0 0 36 44"><path d="M18 42 C8 28 3 21 3 15 A15 15 0 0 1 33 15 C33 21 28 28 18 42Z" fill="none" stroke="#fff" stroke-width="2"/><circle cx="18" cy="15" r="5" fill="none" stroke="#fff" stroke-width="2"/></svg>
    <div><h5>ADDRESS</h5>45 Rua Rainha Ginga, Ingombota<br>Luanda, Angola</div>
  </div>
  <div class="row">
    <svg width="36" height="46" viewBox="0 0 36 46"><rect x="8" y="2" width="20" height="42" rx="3" fill="none" stroke="#fff" stroke-width="2"/><line x1="8" y1="36" x2="28" y2="36" stroke="#fff" stroke-width="2"/><line x1="8" y1="8" x2="28" y2="8" stroke="#fff" stroke-width="2"/></svg>
    <div><h5>PHONE</h5>+244 923 000 417</div>
  </div>
  <div class="row">
    <svg width="36" height="30" viewBox="0 0 36 30"><rect x="1" y="3" width="34" height="24" fill="none" stroke="#fff" stroke-width="2"/><path d="M1 3 L18 17 L35 3 M1 27 L14 14 M35 27 L22 14" fill="none" stroke="#fff" stroke-width="2"/></svg>
    <div><h5>EMAIL</h5>inquiry@lanternbrokers.com</div>
  </div>
</section>

<footer class="abs footer"></footer>
<p class="abs copy">Copyright © 2019 Lantern Brokers. All Rights Reserved.</p>
<div class="abs social foot-social"><span></span><span></span><span></span></div>

</body>
</html>
```